$5 Quest Website Required

I am looking for someone to develop a website akin to the simplicity of www.boxlantern.example with a video in the center or a tab that permits one to "Accept the Challenge."

Incorporates our logo and is used to promote our "$5 Quest Program."

Please see attachments, but we are igniting entrepreneurial spirit among our nation's youth through this interactive and intensive program!

There should be a way to navigate to other sections of the site including:

About
Why
Request $5 Quest Packet
Success Stories
Partners
Link to Norvik Holdings
Updates

Thanks to all in advance!

Looking forward to working with you!

Good feel of what we are looking for in terms of "feel"

http://www.thebrightripple.example/

Thank you,

RB

Please make note of this website, we are going for a feel that is akin to this and less modern and professional...more abstract and interactive...but of course include space for our video:

Colors, feel, imagery, is great. Keep your formats, but bring on the feel!

Thank you all for your hard work and patience.

Thank you all for your hard work thus far.

Meanwhile, please understand that the $5 Quest is young, youthful, full of challenge and vitality, it is a competition among students from high school and universities.  The websites you have delivered are too corporate, stale, and standard.  I'm looking for something that is fresh, different, like www.thebrightripple.example.

Symbols, cartoonish, but serious, down to business and save the world one $5 bill at a time.  The logo can be used as a theme...the colors, the feel.

Video space for explanation on the $5 Quest front and center.  With leaves, $ signs, colorful colors, etc.

Visual needs to be compelling to Join the Challenge! Although Norvik Holdings and the tree is a parent company; $5 Quest is separate and Norvik Holdings should only be mentioned as a link.

PixelHarbor.example in regard to simplicity; and www.thebrightripple.example in terms of style.

Thank you,

Raphael

Like the designs that have been submitted; we are almost there.

Target Market(s)

Professors, students, teachers, parents and NGO leaders who wish to use our program as a way to inspire leadership/entrepreneurship/fundraise for their causes.

Requirements
Must have
• Place for the video, front and center
Include logo
Forsight for blogging, message, etc.
Nice to have
• Plan "buckets" to include"
Explanation Video
Two pamphlets
Contract
FAQs
Website with Blog, voting, registration, video upload, etc.
Flyer perfected
Parable...symbol of our life
Photos
Stats included
Testimonials
Organizations that have used (TKWLM, North Brook Lodge, Marlowton High)
Sponsors (Open Lantern, Copperleaf Learningfield)
Photos from events

I understand this takes coding and such, but want you to be aware of the long term vision for it!

```html
<!DOCTYPE html>
<html lang="en">
<head>
<meta charset="utf-8">
<title>$5 Quest</title>
<link rel="stylesheet" href="https://fonts.googleapis.com/css2?family=Signika:wght@300;400;600&family=Arimo:wght@400;700&display=swap">
<style>
:root{
  --green-dark:#1c8f3a;
  --green:#3aa845;
  --green-light:#7cc242;
  --leaf:#8cc63f;
  --ink:#111;
  --text:#555;
  --panel:#f3f3f3;
  --gallery:#e0e0e0;
  --video:#3b3b3b;
  --rule:#d8d8d8;
  --button:#2aaa4a;
}
*{box-sizing:border-box;margin:0;padding:0}
html,body{width:845px;height:1200px;overflow:hidden;background:#fff}
body{position:relative;font-family:"Arimo",Arial,sans-serif;color:var(--text)}
.page{position:absolute;left:72px;top:0;width:710px;height:1200px;background:#fff;box-shadow:0 0 14px rgba(0,0,0,.28)}
.abs{position:absolute}
.heading{font-family:"Signika",sans-serif;font-weight:400;color:var(--ink);white-space:nowrap}

.brand{left:18px;top:20px;display:flex;align-items:center;gap:8px}
.brand-dot{width:30px;height:30px;border-radius:50%;background:var(--leaf)}
.brand-name{font-family:"Signika",sans-serif;font-weight:600;font-size:28px;color:var(--green-dark)}

.search{left:477px;top:40px;width:224px;height:24px;display:flex;border:1px solid #ccc;background:#fff}
.search-field{flex:1;font-size:9px;color:#999;padding:6px 5px}
.search-btn{width:24px;background:var(--green-light);display:flex;align-items:center;justify-content:center}

.nav{left:8px;top:87px;width:694px;height:33px;background:linear-gradient(#1f9a3c,#6abf48);font-family:"Signika",sans-serif;font-weight:300;font-size:13.5px}
.nav a{position:absolute;top:0;color:#fff;text-decoration:none;height:33px;line-height:33px;white-space:nowrap}
.nav .active{left:0;width:73px;text-align:center;background:#1a7d32}

.hero{left:8px;top:120px;width:694px;height:319px;background:radial-gradient(ellipse at 50% 72%,#5a9a2e 0,#7fae49 16%,#e8ebe6 36%,#f4f4f4 70%,#e6e6e6 100%);border-bottom:2px solid #ddd}
.hero-title{right:23px;top:132px;font-size:42px;line-height:1.1}

.welcome-title{left:21px;top:455px;font-size:18px}
.welcome-text{left:17px;top:494px;width:416px;font-size:8.3px;line-height:17px;text-align:justify;color:var(--text)}
.partner-mark{float:left;width:240px;height:118px;margin:0 12px 0 0;display:flex;align-items:center;justify-content:center;gap:8px}
.partner-mark span{font-family:"Signika",sans-serif;font-size:22px;color:#2f7d2b;white-space:nowrap}
.partner-mark i{width:16px;height:16px;background:var(--green);display:block}

.video{left:456px;top:461px;width:239px;height:202px;background:var(--video);display:flex;align-items:center;justify-content:center}

.gallery-title{left:21px;top:682px;font-size:18px}
.gallery{left:19px;top:717px;width:677px;height:126px;background:var(--gallery)}
.thumb{top:17px;width:138px;height:91px;background:#fff}
.arrow{top:50px}

.col-head{top:860px;display:flex;align-items:flex-end;gap:8px;font-family:"Signika",sans-serif;font-size:18px;color:var(--ink);white-space:nowrap}
.icon{width:30px;height:30px;border-radius:4px}
.panel{left:19px;top:890px;width:677px;height:246px;background:var(--panel)}
.col{top:0;height:246px;padding-top:18px}
.col + .col{border-left:1px solid var(--rule)}
.post-title{font-size:9.6px;font-weight:700;color:#555}
.post-date{font-size:7.5px;color:#666;margin:4px 0 2px}
.post-body{font-size:8.3px;line-height:15.5px;text-align:justify;color:var(--text)}
.news-date{font-family:"Signika",sans-serif;font-weight:300;font-size:12.5px;color:#555;margin-bottom:3px}
.quote{font-size:8.3px;line-height:15.5px;text-align:justify;color:var(--text)}
.quote-by{text-align:right;font-size:8.3px;margin-top:2px;color:var(--text)}
.more{width:48px;height:16px;border-radius:3px;background:var(--button);color:#fff;font-size:7px;text-align:center;line-height:16px;top:220px}

.footer-links{left:0;width:710px;top:1152px;text-align:center;font-family:"Signika",sans-serif;font-weight:300;font-size:9.5px;color:var(--ink)}
.copyright{left:0;width:710px;top:1172px;text-align:center;font-size:8.5px;color:#222}
</style>
</head>
<body>
<div class="page">

  <div class="abs brand"><span class="brand-dot"></span><span class="brand-name">$5 Quest</span></div>

  <div class="abs search">
    <div class="search-field">Search</div>
    <div class="search-btn"><svg width="10" height="10" viewBox="0 0 10 10"><circle cx="4" cy="4" r="2.8" fill="none" stroke="#fff" stroke-width="1.4"/><line x1="6" y1="6" x2="9" y2="9" stroke="#fff" stroke-width="1.4"/></svg></div>
  </div>

  <nav class="abs nav">
    <a class="active" href="#">About</a>
    <a href="#" style="left:107px">Why</a>
    <a href="#" style="left:187px">Request $5 Quest Packet</a>
    <a href="#" style="left:380px">Success Stories</a>
    <a href="#" style="left:505px">Partners</a>
    <a href="#" style="left:594px">Norvik Holdings</a>
  </nav>

  <div class="abs hero" role="img" aria-label="Seedling growing through a gap in white puzzle pieces"></div>
  <h1 class="abs heading hero-title">The 5 Dollar Quest</h1>

  <h2 class="abs heading welcome-title">Welcome</h2>
  <div class="abs welcome-text">
    <div class="partner-mark"><i></i><span>Norvik Holdings</span></div>
    A recent phenomenon, lead by social enterprise Norvik Holdings in collaboration with Copperleaf Learningfield and Halvern University, called “The 5 Dollar Quest” is sweeping across high school and student entrepreneurship organizations across the country and challenging students to put their entrepreneurial genius to work in order to multiply their “$5 nH Factor” as many times as possible for thebenefit of their local community. The movement is aimed at raising funds for local causes and engaging students in a creative way that engages their local community.
  </div>

  <div class="abs video" aria-label="Video player">
    <svg width="28" height="46" viewBox="0 0 28 46"><polygon points="0,0 28,23 0,46" fill="#fff"/></svg>
  </div>

  <h2 class="abs heading gallery-title">Photo Gallery</h2>
  <div class="abs gallery">
    <svg class="abs arrow" style="left:12px" width="22" height="26" viewBox="0 0 22 26"><polyline points="17,3 6,13 17,23" fill="none" stroke="#8a8a8a" stroke-width="5"/></svg>
    <div class="abs thumb" style="left:63px"></div>
    <div class="abs thumb" style="left:262px"></div>
    <div class="abs thumb" style="left:461px"></div>
    <svg class="abs arrow" style="left:645px" width="22" height="26" viewBox="0 0 22 26"><polyline points="5,3 16,13 5,23" fill="none" stroke="#8a8a8a" stroke-width="5"/></svg>
  </div>

  <div class="abs col-head" style="left:18px"><div class="icon" role="img" aria-label="Blog icon with pencil" style="background:linear-gradient(#eee,#6cbf3c)"></div>Blog</div>
  <div class="abs col-head" style="left:264px"><div class="icon" role="img" aria-label="Megaphone news icon" style="background:linear-gradient(#d33,#999)"></div>News</div>
  <div class="abs col-head" style="left:496px"><div class="icon" role="img" aria-label="Speech bubble testimonial icon" style="background:linear-gradient(#ffd23a,#f09a10);border-radius:50%"></div>Testimonials</div>

  <div class="abs panel">
    <div class="abs col" style="left:0;width:235px;padding-left:14px;padding-right:14px">
      <div class="post-title">Lorem Ipsum is simply dummy text</div>
      <div class="post-date">Posted on June 14, 2012</div>
      <div class="post-body">Lorem Ipsum is simply dummy text of the printing and typesetting industry. scrambled it to make a type specimen book.</div>
      <div class="post-title" style="margin-top:30px">Lorem Ipsum is simply dummy text</div>
      <div class="post-date">Posted on June 14, 2012</div>
      <div class="post-body">Lorem Ipsum is simply dummy text of the printing and typesetting industry. scrambled it to make a type specimen book.</div>
      <div class="abs more" style="left:164px">MORE</div>
    </div>
    <div class="abs col" style="left:235px;width:235px;padding-left:18px;padding-right:16px;padding-top:16px">
      <div class="news-date">12-05-2012</div>
      <div class="post-body">Lorem Ipsum is simply dummy text of the printing and typesetting industry. Lorem Ipsum has been the industry's standard dummy text ever since the 1500s, when an unknown printer took a galley of type and scrambled it to make a type specimen book.</div>
      <div class="news-date" style="margin-top:14px">12-05-2012</div>
      <div class="post-body">Lorem Ipsum is simply dummy text of the printing and typesetting industry. scrambled it to make a type specimen book.</div>
      <div class="abs more" style="left:166px">MORE</div>
    </div>
    <div class="abs col" style="left:470px;width:207px;padding-left:15px;padding-right:10px">
      <div class="quote">“Lorem Ipsum is simply dummy text of the printing and typesetting industry. Lorem Ipsum has been the industry's standard dummy text”</div>
      <div class="quote-by">- Lorem Ipsum</div>
      <div class="quote" style="margin-top:16px">“Lorem Ipsum is simply dummy text of the printing and typesetting industry. Lorem Ipsum has been the industry's standard dummy text”</div>
      <div class="quote-by">- Lorem Ipsum</div>
      <div class="abs more" style="left:155px">MORE</div>
    </div>
  </div>

  <div class="abs footer-links">About | Why | Request $5 Quest Packet | Success Stories | Partners | Norvik Holdings</div>
  <div class="abs copyright">© 2012. All Rights Reserved.</div>

</div>
</body>
</html>
```